Copperbend Blazeworks Website Design

I am looking for a website design ( Home page and inner template page ) in a .psd format. The home page needs to have a large hero image what will function as a "slider", and have some highlight graphical areas/links to the following links "Public & Municipal Events", "Corporate Events", "Special Events". The main navigation needs to have the following nav links "gallery", "home", "about", "services" and "contact". Unfortunately the client does not have any nice hi-rez images ( this is a company that specializes is large fireworks displays ) so please use stock photography sample images from snapvaultpics since we have an account there an can purchase the photos if our client wants to use them. Our current full time graphic artist has been with us for a long time so we are looking at artflockhub as a way to add a fresh approach to design and possibly find someone we can work with regularly. Here is a few designs that in the way we display them for our clients for approval. As you can see there are a couple that don't have their own images so they are utilizing the before mentioned snapvaultpics samples. On the plus side we did manage to get their logo in a .ai format. We have our team for handling the conversion from design to html.

http://reedfoxbuildstudio.com/dev/

```html
<!DOCTYPE html>
<html lang="en">
<head>
<meta charset="utf-8">
<title>Copperbend Blazeworks</title>
<link rel="stylesheet" href="https://fonts.googleapis.com/css2?family=Tinos&family=Roboto:wght@400;500&family=Lato:wght@400;700&display=swap">
<style>
:root{
  --blue:#4aabdf;
  --ink:#111;
  --text:#444;
  --line:#e3e3e3;
  --footer:#0d0d0d;
  --white:#fff;
}
*{box-sizing:border-box;margin:0;padding:0}
html,body{width:1200px;height:3477px;overflow:hidden}
body{position:relative;background:var(--white);font-family:'Roboto',sans-serif;color:var(--text)}
.abs{position:absolute}
.serif{font-family:'Tinos',serif;font-weight:400}
/* header */
.topbar{left:290px;top:0;width:910px;height:43px;background:var(--blue);clip-path:polygon(0 0,100% 0,100% 100%,32px 100%);color:var(--white);font-size:16px;font-weight:500;display:flex;align-items:center;justify-content:flex-end;padding-right:20px;gap:12px}
.topbar .dot{width:13px;height:13px;border-radius:50%;background:var(--white)}
.logo{display:flex;flex-direction:column;align-items:center;gap:8px;text-align:center;font-family:'Tinos',serif;font-size:19px;line-height:22px;white-space:nowrap}
.site-logo{left:70px;top:14px;width:200px;color:#333}
.logo .mark{width:36px;height:36px;border-radius:50%;background:var(--blue)}
.mainnav{left:364px;top:62px;width:720px;display:flex;justify-content:space-between;font-size:17px;font-weight:500;color:var(--ink)}
/* hero */
.hero{left:0;top:101px;width:1200px;height:604px;background:radial-gradient(ellipse at 45% 20%,#b23a9a 0%,#5a2a8a 30%,transparent 60%),linear-gradient(180deg,#2a1d5c 0%,#7b2f7c 45%,#e0505f 75%,#f08a3a 88%,#111 100%)}
.hero-title{left:104px;top:308px;font-size:54px;line-height:54px;color:var(--white);white-space:nowrap}
.btn{display:flex;align-items:center;justify-content:center;background:var(--blue);color:var(--white);font-weight:500;border-radius:4px;font-size:16px}
.hero-cta{left:104px;top:436px;width:163px;height:51px}
.dots{left:557px;top:665px;display:flex;gap:11px}
.dots i{width:12px;height:12px;border-radius:50%;background:#888}
.dots i:first-child{background:var(--white)}
/* sections */
.sec-title{left:0;width:1200px;text-align:center;font-size:42px;color:var(--ink)}
.sec-sub{left:0;width:1200px;text-align:center;font-size:15px;line-height:26px;color:#333}
.card{top:906px;width:314px;height:410px;border:1px solid var(--line);text-align:center}
.card .photo{height:204px}
.card h3{font-family:'Lato',sans-serif;font-weight:500;font-size:24px;color:var(--ink);margin-top:16px}
.card p{font-size:13.5px;line-height:26px;margin:10px 20px 0;color:#555}
.btn-line{position:absolute;left:86px;top:348px;width:142px;height:46px;border:2px solid var(--blue);border-radius:5px;color:var(--blue);font-size:15px;display:flex;align-items:center;justify-content:center}
/* about */
.about{left:0;top:1403px;width:1200px;height:494px;background:radial-gradient(circle at 78% 38%,#c7b6ff 0%,#6b46d6 18%,#2c2a8f 40%,#0f1a4a 70%,#081028 100%)}
.about-box{left:132px;top:1481px;width:364px;height:344px;background:var(--white);border-radius:6px;padding:26px 22px 0 24px}
.about-box h2{font-size:35px;line-height:38px;color:var(--ink)}
.about-box p{font-size:13px;line-height:25.7px;margin-top:8px;color:#555;letter-spacing:-0.1px}
.about-cta{position:absolute;left:25px;top:267px;width:165px;height:53px}
/* gallery */
.tile{width:239px;height:198px}
/* contact */
.contact{left:0;top:2584px;width:1200px;height:660px;background:linear-gradient(180deg,#141414 0%,#1b1f2a 60%,#121826 100%)}
.contact-head{left:136px;color:var(--white);font-size:26px}
.info{left:137px;top:2748px;color:var(--white);font-size:16px;line-height:30px}
.social{left:132px;top:2957px;display:flex;gap:14px}
.social i{width:52px;height:52px;border:2px solid var(--white);border-radius:50%;display:block}
.field{color:var(--white)}
.field label{display:block;font-size:14px;margin-bottom:5px}
.field .box{background:var(--white);height:42px}
/* footer */
.footer{left:0;top:3244px;width:1200px;height:233px;background:var(--footer)}
.foot-logo{left:450px;top:3282px;width:300px;color:var(--white)}
.footnav{left:237px;top:3396px;width:726px;display:flex;justify-content:space-between;font-size:17px;font-weight:500;color:var(--white)}
.copyright{left:0;top:3440px;width:1200px;text-align:center;color:var(--white);font-size:14px}
</style>
</head>
<body>

<header>
  <div class="abs topbar">
    <svg width="15" height="15" viewBox="0 0 24 24"><path fill="#fff" d="M6.6 10.8a15 15 0 0 0 6.6 6.6l2.2-2.2c.3-.3.7-.4 1-.2 1.1.4 2.3.6 3.6.6.6 0 1 .4 1 1V20c0 .6-.4 1-1 1A17 17 0 0 1 3 4c0-.6.4-1 1-1h3.5c.6 0 1 .4 1 1 0 1.3.2 2.5.6 3.6.1.3 0 .7-.2 1z"/></svg>
    <span>What do I need for my event?</span><span>|</span><span>(888) 888-8888</span><span>|</span>
    <span class="dot"></span><span class="dot"></span><span class="dot"></span>
  </div>
  <div class="abs logo site-logo"><span class="mark"></span><span>Copperbend Blazeworks</span></div>
  <nav class="abs mainnav"><span>HOME</span><span>|</span><span>GALLERY</span><span>|</span><span>ABOUT</span><span>|</span><span>SERVICES</span><span>|</span><span>CONTACT</span></nav>
</header>

<section>
  <div class="abs hero" role="img" aria-label="Fireworks bursting over a field with a family watching in silhouette"></div>
  <svg class="abs" style="left:50px;top:380px" width="24" height="44"><path d="M22 2 2 22l20 20" stroke="#fff" stroke-width="2" fill="none"/></svg>
  <svg class="abs" style="left:1110px;top:380px" width="24" height="44"><path d="M2 2l20 20L2 42" stroke="#fff" stroke-width="2" fill="none"/></svg>
  <h1 class="abs serif hero-title">We'll Help You Make<br>the Magic Happen</h1>
  <div class="abs btn hero-cta">GET STARTED</div>
  <div class="abs dots"><i></i><i></i><i></i><i></i></div>
</section>

<section>
  <h2 class="abs sec-title serif" style="top:778px">OUR SERVICES</h2>
  <p class="abs sec-sub" style="top:829px">Lorem ipsum dolor sit amet, consectetur adipiscing elit, sed do eiusmod<br>tempor incididunt ut labore et dolore magna aliqua.</p>
  <div class="abs card" style="left:103px">
    <div class="photo" role="img" aria-label="Fireworks over a city skyline at night" style="background:linear-gradient(180deg,#1a2070,#7b3a9a 55%,#1a1a50)"></div>
    <h3>Public &amp; Municipal Events</h3>
    <p>Lorem ipsum dolor sit amet, coetur adipiscing elit, sed do eiusmod teor incididunt ut labore et dolore magna aliqua.</p>
    <div class="btn-line">LEARN MORE</div>
  </div>
  <div class="abs card" style="left:439px">
    <div class="photo" role="img" aria-label="Fireworks over a harbour with boats" style="background:linear-gradient(180deg,#0d0d14,#4a3a5a 55%,#2a2030)"></div>
    <h3>Corporate Events</h3>
    <p>Lorem ipsum dolor sit amet, coetur adipiscing elit, sed do eiusmod teor incididunt ut labore et dolore magna aliqua.</p>
    <div class="btn-line">LEARN MORE</div>
  </div>
  <div class="abs card" style="left:775px">
    <div class="photo" role="img" aria-label="Crowd watching fireworks in a smoky sky" style="background:linear-gradient(180deg,#1e4a56,#3b6b70 50%,#0c1416)"></div>
    <h3>Special Events</h3>
    <p>Lorem ipsum dolor sit amet, coetur adipiscing elit, sed do eiusmod teor incididunt ut labore et dolore magna aliqua.</p>
    <div class="btn-line">LEARN MORE</div>
  </div>
</section>

<section>
  <div class="abs about" role="img" aria-label="Crowd watching blue and purple fireworks at night"></div>
  <div class="abs about-box">
    <h2 class="serif">ABOUT US</h2>
    <p>Lorem ipsum dolor sit amet, consectetur adipiscing elit, sed do eiusmod tempor incididunt ut labore et dolore magna aliqua. Quis um suspendisse ultrices gravida. Risus commos accumsan lacus vel facilisis. Lorem ipsum dolor sit amet, consectetur adipiscing elit, sed do eiusmod tempor incididunt ut labore et dolore magna aliqua.</p>
    <div class="btn about-cta">LEARN MORE</div>
  </div>
</section>

<section>
  <h2 class="abs sec-title serif" style="top:1973px">OUR GALLERY</h2>
  <p class="abs sec-sub" style="top:2024px">Lorem ipsum dolor sit amet, consectetur adipiscing elit, sed do eiusmod<br>tempor incididunt ut labore et dolore magna aliqua.</p>
  <div class="abs tile" style="left:103px;top:2093px;background:linear-gradient(180deg,#3b2a8a,#c2477a 60%,#151515)" role="img" aria-label="Family watching fireworks"></div>
  <div class="abs tile" style="left:351px;top:2093px;background:radial-gradient(circle at 50% 40%,#f2a23a,#5a3a8a 60%,#0d0d1a)" role="img" aria-label="Golden and blue fireworks"></div>
  <div class="abs tile" style="left:601px;top:2093px;background:radial-gradient(circle at 50% 50%,#c23a5a,#2a1420 65%,#0a0a0a)" role="img" aria-label="Red fireworks display"></div>
  <div class="abs tile" style="left:849px;top:2093px;background:linear-gradient(180deg,#1a1a3a,#3a4aa0 50%,#c0607a)" role="img" aria-label="Firework rockets launching"></div>
  <div class="abs tile" style="left:103px;top:2302px;background:radial-gradient(circle at 50% 50%,#d07a3a,#5a2a6a 60%,#0d0a14)" role="img" aria-label="Colourful fireworks"></div>
  <div class="abs tile" style="left:351px;top:2302px;background:radial-gradient(circle at 50% 40%,#8a6a3a,#20182a 65%,#0a0a10)" role="img" aria-label="Fireworks over a crowd"></div>
  <div class="abs tile" style="left:601px;top:2302px;background:linear-gradient(180deg,#1c2230,#4a4a5a 60%,#b0a0a0)" role="img" aria-label="Fireworks over a snowy town"></div>
  <div class="abs tile" style="left:849px;top:2302px;background:radial-gradient(circle at 50% 40%,#c0502a,#3a1a10 60%,#0a0805)" role="img" aria-label="Orange fireworks"></div>
</section>

<section>
  <div class="abs contact" role="img" aria-label="Night city skyline"></div>
  <h4 class="abs serif contact-head" style="top:2646px">CONTACT</h4>
  <p class="abs" style="left:138px;top:2684px;color:#fff;font-size:15px;line-height:26px">Thank you for your interest. We look forward<br>to hearing from you soon.</p>
  <div class="abs info">
    <div>&#9743;&nbsp; Toll-free: 888 - 888 - 8888</div>
    <div>&#9743;&nbsp; Tel: 123 - 456 - 7890</div>
    <div>&#9113;&nbsp; Fax: 000 - 000 - 0000</div>
    <div>&#9993;&nbsp; Email: info@copperbendblazeworks.com</div>
  </div>
  <h4 class="abs serif contact-head" style="top:2908px">FOLLOW US</h4>
  <div class="abs social"><i></i><i></i><i></i><i></i></div>

  <div class="abs field" style="left:568px;top:2674px;width:212px"><label>Name</label><div class="box"></div></div>
  <div class="abs field" style="left:787px;top:2674px;width:212px"><label>Phone</label><div class="box"></div></div>
  <div class="abs field" style="left:568px;top:2753px;width:431px"><label>Email*</label><div class="box"></div></div>
  <div class="abs field" style="left:568px;top:2832px;width:212px"><label>Event or Organization</label><div class="box"></div></div>
  <div class="abs field" style="left:787px;top:2832px;width:212px"><label>Event Location - City/State</label><div class="box"></div></div>
  <div class="abs field" style="left:568px;top:2911px;width:212px"><label>Display Date, Time, Budget</label><div class="box"></div></div>
  <div class="abs field" style="left:787px;top:2911px;width:212px"><label>Display Type &amp; Duration</label><div class="box"></div></div>
  <div class="abs field" style="left:568px;top:2990px;width:431px"><label>Message/Special Requests*</label><div class="box" style="height:94px"></div></div>
  <div class="abs btn" style="left:836px;top:3123px;width:163px;height:52px">SUBMIT</div>
</section>

<footer>
  <div class="abs footer"></div>
  <div class="abs logo foot-logo"><span class="mark"></span><span>Copperbend Blazeworks</span></div>
  <nav class="abs footnav"><span>HOME</span><span>|</span><span>GALLERY</span><span>|</span><span>ABOUT</span><span>|</span><span>SERVICES</span><span>|</span><span>CONTACT</span></nav>
  <p class="abs copyright">© 2021 Copperbend Blazeworks . All Rights Reserved.</p>
</footer>

</body>
</html>
```